Brightway Carpet and Tile cleaning Business card Design

I need a design that has the same feel as my van.
i would also like a prominent "Review us on facebook" somewhere, but not that it makes it look silly.
I would like the card to have a little bit of grey or black in the design as well.

It will need contact details
phone: 0455 817264
email: rkbrightwayclean@mailbox-example.com
website: www.brightwaycarpetandtilecleaning-example.com.au
facebook: /brightwaycarpetandtilecleaning

Industry/Entity Type

Business

Contact Information for Business Card

Phone number 0455817264
Email rkbrightwayclean@mailbox-example.com
Website www.brightwaycarpetandtilecleaning-example.com.au
Facebook/brightwaycarpetandtilecleaning

Colors
000000

Requirements
Must have
• Same feel as my van
• I want the card to stand out from the crowd
Nice to have
• Maybe include a tiny bit of a third colour? Grey's,blacks, orange?

```html
<!DOCTYPE html>
<html lang="en">
<head>
<meta charset="utf-8">
<title>Brightway Carpet and Tile cleaning – Business Card</title>
<link rel="stylesheet" href="https://fonts.googleapis.com/css2?family=Exo+2:wght@500;700&family=Open+Sans:wght@400;600&display=swap">
<style>
  :root {
    --stage: #3b3b3b;
    --white: #ffffff;
    --aqua: #1fb5e2;
    --aqua-deep: #0f9ccb;
    --aqua-soft: #7fd6f2;
    --lime: #8cc63f;
    --lime-soft: #c6e58f;
    --steel: #8e9196;
    --steel-dark: #5d6066;
    --ink: #0b0b0b;
    --button-top: #8fa6dc;
    --button-bottom: #3d5fae;
    --button-text: #0c1a3a;
  }
  * { box-sizing: border-box; margin: 0; padding: 0; }
  html, body { width: 1105px; height: 1200px; overflow: hidden; }
  body { background: var(--stage); position: relative; font-family: "Open Sans", Arial, sans-serif; }

  .card {
    position: absolute;
    left: 196px;
    width: 720px;
    height: 410px;
    overflow: hidden;
    box-shadow: 0 4px 14px rgba(0,0,0,.45);
  }
  .card--front { top: 146px; background: var(--white); }
  .card--back  { top: 602px; background: var(--ink); }

  .card__wave { position: absolute; inset: 0; width: 720px; height: 410px; }

  .brand {
    position: absolute;
    display: flex;
    align-items: center;
    gap: 12px;
    font-family: "Exo 2", Arial, sans-serif;
    font-weight: 700;
    letter-spacing: -0.5px;
  }
  .brand__dot { border-radius: 50%; background: var(--aqua); flex: none; }
  .card--front .brand { left: 44px; top: 82px; font-size: 58px; color: var(--aqua-deep); }
  .card--front .brand__dot { width: 22px; height: 22px; }
  .card--back .brand { left: 0; right: 0; top: 160px; justify-content: center; font-size: 66px; color: var(--aqua); }
  .card--back .brand__dot { width: 26px; height: 26px; }

  .contact {
    position: absolute;
    right: 26px;
    top: 196px;
    text-align: right;
    color: var(--white);
  }
  .contact__name {
    font-family: "Exo 2", Arial, sans-serif;
    font-weight: 700;
    font-size: 27px;
    letter-spacing: 0.5px;
    margin-right: 10px;
  }
  .contact__role {
    font-family: "Exo 2", Arial, sans-serif;
    font-weight: 500;
    font-size: 19px;
    letter-spacing: 0.5px;
    margin: 2px 10px 18px 0;
  }
  .contact__list { list-style: none; }
  .contact__item {
    display: flex;
    justify-content: flex-end;
    align-items: center;
    gap: 14px;
    font-size: 16px;
    height: 31px;
  }
  .contact__icon { width: 18px; height: 18px; flex: none; }

  .card__bokeh {
    position: absolute;
    inset: 0;
    background:
      radial-gradient(circle at 12% 22%, rgba(70,90,70,.35) 0 40px, transparent 41px),
      radial-gradient(circle at 30% 70%, rgba(60,80,60,.3) 0 55px, transparent 56px),
      radial-gradient(circle at 82% 30%, rgba(70,90,70,.3) 0 45px, transparent 46px),
      radial-gradient(circle at 88% 82%, rgba(60,85,60,.35) 0 60px, transparent 61px),
      radial-gradient(circle at 55% 85%, rgba(60,80,60,.25) 0 48px, transparent 49px),
      linear-gradient(115deg, transparent 0 46%, rgba(255,255,255,.14) 52%, rgba(255,255,255,.05) 64%, transparent 80%);
  }

  .review {
    position: absolute;
    left: 200px;
    top: 323px;
    display: flex;
    align-items: center;
    gap: 8px;
  }
  .review__label {
    width: 260px;
    height: 40px;
    border-radius: 4px;
    background: linear-gradient(var(--button-top), var(--button-bottom));
    border: 1px solid #9db2e6;
    color: var(--button-text);
    font-family: "Exo 2", Arial, sans-serif;
    font-weight: 700;
    font-size: 26px;
    line-height: 38px;
    text-align: center;
  }
  .review__square {
    width: 48px;
    height: 48px;
    border-radius: 6px;
    background: linear-gradient(var(--button-top), var(--button-bottom));
    border: 1px solid #9db2e6;
  }
</style>
</head>
<body>

<section class="card card--front" aria-label="Business card front">
  <svg class="card__wave" viewBox="0 0 720 410" aria-hidden="true">
    <defs>
      <linearGradient id="aquaFill" x1="0" y1="0" x2="0" y2="1">
        <stop offset="0" stop-color="#33c2ec"/>
        <stop offset="1" stop-color="#1aaedc"/>
      </linearGradient>
      <linearGradient id="steelFill" x1="0" y1="0" x2="1" y2="0">
        <stop offset="0" stop-color="#b9bcc0"/>
        <stop offset="1" stop-color="#6d7075"/>
      </linearGradient>
    </defs>
    <path d="M0 270 C150 300 300 290 420 200 C520 130 620 118 720 120 L720 112 C610 110 510 118 410 190 C300 270 150 282 0 258 Z" fill="url(#steelFill)"/>
    <path d="M0 270 C130 300 250 312 380 262 C250 318 120 322 0 312 Z" fill="var(--lime)"/>
    <path d="M0 280 C120 300 230 304 330 280 C230 306 110 310 0 300 Z" fill="var(--lime-soft)" opacity=".8"/>
    <path d="M0 314 C140 326 280 320 420 230 C520 165 620 126 720 128 L720 410 L0 410 Z" fill="url(#aquaFill)"/>
    <rect x="0" y="120" width="720" height="290" fill="url(#aquaFill)" opacity="0" role="img" aria-label="Soft bubble texture across the blue wave"/>
  </svg>

  <div class="brand">
    <span class="brand__name">Brightway</span>
    <span class="brand__dot"></span>
  </div>

  <div class="contact">
    <p class="contact__name">RICK KOWALSKI</p>
    <p class="contact__role">OWNER/OPERATOR</p>
    <ul class="contact__list">
      <li class="contact__item">
        <span>0455817264</span>
        <svg class="contact__icon" viewBox="0 0 18 18" aria-hidden="true"><path d="M4 2 L7 2 L8 6 L6 7.5 C7 10 8 11 10.5 12 L12 10 L16 11 L16 14 C16 15 15 16 14 16 C8 16 2 10 2 4 C2 3 3 2 4 2 Z" fill="#fff"/></svg>
      </li>
      <li class="contact__item">
        <span>rkbrightwayclean@mailbox-example.com</span>
        <svg class="contact__icon" viewBox="0 0 18 18" aria-hidden="true"><rect x="2" y="4" width="14" height="10" fill="#fff"/><path d="M2 4 L9 10 L16 4" fill="none" stroke="#1aaedc" stroke-width="1.4"/></svg>
      </li>
      <li class="contact__item">
        <span>www.brightwaycarpetandtilecleaning-example.com.au</span>
        <svg class="contact__icon" viewBox="0 0 18 18" aria-hidden="true"><circle cx="9" cy="9" r="7" fill="#fff"/><path d="M2 9 H16 M9 2 C5 6 5 12 9 16 M9 2 C13 6 13 12 9 16" fill="none" stroke="#1aaedc" stroke-width="1.2"/></svg>
      </li>
      <li class="contact__item">
        <span>/brightwaycarpetandtilecleaning</span>
        <svg class="contact__icon" viewBox="0 0 18 18" aria-hidden="true"><rect x="2" y="2" width="14" height="14" fill="#fff"/></svg>
      </li>
    </ul>
  </div>
</section>

<section class="card card--back" aria-label="Business card back">
  <div class="card__bokeh" role="img" aria-label="Dark glowing bubble texture with a diagonal sheen"></div>

  <div class="brand">
    <span class="brand__name">Brightway</span>
    <span class="brand__dot"></span>
  </div>

  <div class="review">
    <span class="review__label">REVIEW US ON</span>
    <span class="review__square"></span>
  </div>
</section>

</body>
</html>
```